Heater product information sheets

I need the two product information sheets organized and laid out in a clean, easy to read attractive manner. These sheets are to advertise propane heaters for outdoor use and for wholesale to propane distributors, restaurants and homeowners that need to have propane heat as the winter ends and spring begins. They will be used for chilly evenings when people want to be outside eating, drinking and being social.

Target Market(s)

Restaurants, hospitality industry, special events, party rental companies, home owners with backyards

Font styles to use
Sans Serif

Requirements
Must have
• My logo in the document instead of t. Marlow and company
Nice to have
• I would like to see Fire illustrated coming up the heaters and on the round glass, show it up the middle of the glass tube propane heater.

```html
<!DOCTYPE html>
<html lang="en">
<head>
<meta charset="utf-8">
<title>Adjustable Propane Heater – Product Sheet</title>
<link href="https://fonts.googleapis.com/css2?family=Signika:wght@300;400;600;700&display=swap" rel="stylesheet">
<style>
  :root{
    --red:#d0524f;
    --ink:#3d4454;
    --text:#2b2b2b;
    --gold:#e2b36a;
    --sand:#f1dcbf;
    --line:#ecd2ad;
    --teal:#7aa6a0;
    --paper:#ffffff;
  }
  html,body{margin:0;padding:0;overflow:hidden;background:var(--paper);}
  .sheet{position:relative;width:848px;height:1200px;overflow:hidden;background:var(--paper);
    font-family:"Signika",sans-serif;color:var(--text);}
  .abs{position:absolute;}
  .decor{position:absolute;inset:0;width:848px;height:1200px;}
  .title{left:102px;top:72px;margin:0;line-height:1;}
  .title-main{display:block;font-size:66px;font-weight:700;color:var(--red);letter-spacing:-1px;}
  .title-sub{display:block;font-size:40px;font-weight:600;color:var(--ink);margin-top:8px;}
  .brand{left:560px;top:108px;width:240px;text-align:center;font-size:34px;font-weight:700;color:var(--text);letter-spacing:.5px;line-height:1.1;}
  .brand-dot{display:inline-block;width:14px;height:14px;background:var(--text);border-radius:50%;margin-right:8px;vertical-align:middle;}
  .product-photo{left:90px;top:214px;width:184px;height:490px;border-radius:40px 40px 18px 18px;
    background:linear-gradient(180deg,#f6c766 0%,#e89a3a 14%,#b9b9b9 20%,#3a3a3a 36%,#1f1f1f 100%);}
  .section-head{margin:0;font-size:27px;font-weight:700;color:var(--red);letter-spacing:.3px;}
  .spec-head{left:339px;top:216px;}
  .detail-head{left:339px;top:403px;}
  .spec{position:absolute;top:266px;width:130px;text-align:center;font-size:13.5px;font-weight:300;line-height:17px;}
  .spec svg{display:block;margin:0 auto 10px;width:40px;height:38px;}
  .details{left:372px;top:458px;margin:0;padding:0;list-style:none;width:420px;font-size:20px;font-weight:300;line-height:23px;}
  .details li{position:relative;padding-left:20px;margin-bottom:10px;}
  .details li::before,.notes li::before{content:"";position:absolute;left:0;top:8px;width:10px;height:10px;border-radius:50%;background:var(--gold);}
  .offer{position:absolute;top:752px;width:100px;text-align:center;font-size:12.5px;font-weight:400;line-height:15.5px;}
  .offer svg{display:block;margin:0 auto 10px;width:58px;height:56px;}
  .note-head{left:62px;top:952px;}
  .notes{left:62px;top:992px;margin:0;padding:0;list-style:none;width:340px;font-size:20px;font-weight:300;line-height:22px;}
  .notes li{position:relative;padding-left:31px;margin-bottom:9px;}
  .price{font-weight:700;color:var(--red);font-size:24px;}
  .contact-head{left:439px;top:952px;}
  .contact{left:442px;top:1000px;font-size:20px;font-weight:300;}
  .contact strong{font-weight:600;}
  .contact-line{position:absolute;left:439px;font-size:20px;font-weight:300;display:flex;align-items:center;white-space:nowrap;}
  .contact-line svg{width:25px;height:25px;margin-right:10px;flex:none;}
</style>
</head>
<body>
<main class="sheet">
  <svg class="decor" viewBox="0 0 848 1200" aria-hidden="true">
    <circle cx="145" cy="183" r="130" fill="var(--gold)"/>
    <circle cx="-52" cy="578" r="128" fill="var(--sand)"/>
    <circle cx="840" cy="1205" r="135" fill="var(--sand)"/>
    <circle cx="655" cy="643" r="323" fill="none" stroke="var(--line)" stroke-width="1"/>
    <circle cx="-60" cy="1290" r="380" fill="none" stroke="var(--line)" stroke-width="1"/>
  </svg>

  <h1 class="abs title"><span class="title-main">Adjustable</span><span class="title-sub">Propane Heater</span></h1>

  <div class="abs brand"><span class="brand-dot"></span>Brightside<br>Rentals</div>

  <div class="abs product-photo" role="img" aria-label="Photo of a black tall patio propane heater with a glowing flame under its round reflector hood"></div>

  <h2 class="abs section-head spec-head">SPECIFICATIONS</h2>

  <div class="spec" style="left:303px">
    <svg viewBox="0 0 40 38" fill="none" stroke="var(--teal)" stroke-width="1.6" stroke-linecap="round" stroke-linejoin="round"><path d="M22 6 14 21h7l-3 11 9-16h-7z"/><path d="M20 1v3M6 19H3M37 19h-3M9 8l2 2M31 8l-2 2M9 30l2-2M31 30l-2-2"/></svg>
    Adjustable up to<br>48,000 BTU</div>
  <div class="spec" style="left:417px">
    <svg viewBox="0 0 40 38" fill="none" stroke="var(--teal)" stroke-width="1.6" stroke-linejoin="round"><path d="M4 4h32l-3 30H7z"/><path d="M9 8h22v10c-3 4-6-2-8 3s-5-1-7 2-5 0-7-3z"/><path d="M8 30h24"/></svg>
    Black Powder<br>Coated Finish</div>
  <div class="spec" style="left:546px">
    <svg viewBox="0 0 40 38" fill="none" stroke="var(--teal)" stroke-width="1.6" stroke-linejoin="round"><rect x="16" y="1" width="8" height="5"/><path d="M14 6h12v4h-12zM12 10h16c2 0 3 2 3 4v18c0 2-1 4-3 4H12c-2 0-3-2-3-4V14c0-2 1-4 3-4z"/><path d="M9 18h22M9 28h22"/></svg>
    Uses 20 lbs.<br>Propane Tank</div>
  <div class="spec" style="left:674px;width:130px">
    <svg viewBox="0 0 40 38" fill="none" stroke="var(--teal)" stroke-width="1.6" stroke-linejoin="round"><path d="M8 4h26v28H6c2 0 2-5 0-5h2z"/><path d="M34 4c3 0 3 5 0 5"/><path d="M16 9l5-2 5 2v4c0 3-2 5-5 6-3-1-5-3-5-6z"/><path d="M13 24h16M13 28h12"/></svg>
    CE, GS, AGA, CSA,<br>with ETL certificate<br>and ROHS approved.</div>

  <h2 class="abs section-head detail-head">ADDITIONAL DETAILS</h2>
  <ul class="abs details">
    <li>Commercial Quality</li>
    <li>For Outdoor Use Only</li>
    <li>Conforms to ANSI STD Z83.26-2014</li>
    <li>Certified to CSA STD 2.37-2014 Gas- fired outdoor infrared patio heaters</li>
    <li>Safety Auto Shut Off Switch</li>
    <li>Thermostatic Control</li>
    <li>Piezoelectric ignition</li>
    <li>Base Diameter 17” - Anti-Tip Design</li>
    <li>Standard Wheels - Tilt &amp; Move</li>
    <li>Run time: 8-10 hours with standard 20 lbs. Propane tank</li>
    <li>88” Tall</li>
    <li>Heating Area: 200 sq. ft</li>
  </ul>

  <div class="offer" style="left:26px">
    <svg viewBox="0 0 58 56" fill="none" stroke="var(--teal)" stroke-width="2.2" stroke-linejoin="round" stroke-linecap="round"><path d="M2 4h6l6 30h36"/><path d="M9 12h44l-4 18H13"/><path d="M20 18h24M22 24h18"/><circle cx="20" cy="46" r="4"/><circle cx="42" cy="46" r="4"/></svg>
    Available to<br>Purchase</div>
  <div class="offer" style="left:143px">
    <svg viewBox="0 0 58 56" fill="none" stroke="var(--teal)" stroke-width="2.2" stroke-linejoin="round"><path d="M22 20 29 4l7 16"/><circle cx="29" cy="5" r="2.5"/><rect x="2" y="20" width="54" height="32" rx="2"/><text x="29" y="43" text-anchor="middle" font-family="Signika,sans-serif" font-size="17" font-weight="400" fill="var(--teal)" stroke="none" letter-spacing="1.5">RENT</text></svg>
    Available to Rent</div>
  <div class="offer" style="left:251px">
    <svg viewBox="0 0 58 56" fill="none" stroke="var(--teal)" stroke-width="2.2" stroke-linejoin="round" stroke-linecap="round"><circle cx="29" cy="5" r="2.5"/><path d="M6 30c0-14 10-22 23-22s23 8 23 22z"/><path d="M4 30h50v5H4z"/><path d="M12 20c3-5 8-7 12-7"/><path d="M4 44h12l8-4h18c2 0 2 3 0 3H30M16 52h14l18-10"/><path d="M2 42v12"/></svg>
    Seasonal Rental Programs for Restaurant and hospitality companies</div>

  <h2 class="abs section-head note-head">NOTE:</h2>
  <ul class="abs notes">
    <li>Price:&nbsp; <span class="price">$250</span> each</li>
    <li>Assembly &amp; Delivery price upon request</li>
    <li>Discounts for large quantity orders</li>
  </ul>

  <h2 class="abs section-head contact-head">For Inquiries and Orders:</h2>
  <p class="abs contact" style="margin:0">Contact: <strong>Dana Whitfield</strong></p>
  <div class="contact-line" style="top:1036px">
    <svg viewBox="0 0 25 25"><circle cx="12.5" cy="12.5" r="12.5" fill="var(--teal)"/><path d="M8 6.5l2.5-.5 1.3 3-1.6 1.2c.7 1.6 1.9 2.8 3.5 3.5l1.2-1.6 3 1.3-.5 2.5c-5.4.3-9.7-4-9.4-9.4z" fill="#fff"/></svg>
    555-014-2298</div>
  <div class="contact-line" style="top:1070px">
    <svg viewBox="0 0 25 25"><circle cx="12.5" cy="12.5" r="12.5" fill="var(--teal)"/><rect x="6.5" y="8" width="12" height="9" fill="none" stroke="#fff" stroke-width="1.3"/><path d="M6.5 8l6 5 6-5" fill="none" stroke="#fff" stroke-width="1.3"/></svg>
    dana@brightsiderentals.com</div>
  <div class="contact-line" style="top:1104px">
    <svg viewBox="0 0 25 25"><circle cx="12.5" cy="12.5" r="12.5" fill="var(--teal)"/><path d="M12.5 5.5a4.5 4.5 0 0 1 4.5 4.5c0 3.5-4.5 8-4.5 8S8 13.5 8 10a4.5 4.5 0 0 1 4.5-4.5z" fill="none" stroke="#fff" stroke-width="1.3"/><circle cx="12.5" cy="10" r="1.6" fill="#fff"/><path d="M8 19.5h9" stroke="#fff" stroke-width="1.3"/></svg>
    42 Mill Street Lakeview, NJ 07000</div>
</main>
</body>
</html>
```